Business Card Design Project

Looking to update our business cards. We have a logo with our slogan. We are an IT firm so we wouldlike a modern look.

Industry/Entity Type

Business

```html
<!DOCTYPE html>
<html lang="en">
<head>
<meta charset="utf-8">
<title>Uptick Inc business card</title>
<link rel="stylesheet" href="https://fonts.googleapis.com/css2?family=Arimo:wght@400;700&family=Montserrat:wght@500;600&display=swap">
<style>
  :root {
    --backdrop: #ece9e4;
    --card: #ffffff;
    --green-dark: #66823f;
    --green-light: #a9c23f;
    --ink: #222222;
    --ink-soft: #555555;
    --rule: #bbbbbb;
  }
  * { box-sizing: border-box; margin: 0; padding: 0; }
  html, body { width: 1200px; height: 695px; overflow: hidden; }
  body {
    background: var(--backdrop);
    font-family: "Arimo", Arial, sans-serif;
    color: var(--ink);
    position: relative;
  }
  .card {
    position: absolute;
    top: 190px;
    width: 530px;
    height: 310px;
    background: var(--card);
    box-shadow: 0 6px 18px rgba(0,0,0,0.18);
    overflow: hidden;
  }
  .card--front { left: 55px; }
  .card--back { left: 615px; }

  /* Front */
  .brand {
    position: absolute;
    left: 0; right: 0; top: 40px;
    text-align: center;
  }
  .brand__name {
    font-family: "Montserrat", sans-serif;
    font-weight: 600;
    font-size: 56px;
    letter-spacing: 8px;
    color: var(--green-dark);
    line-height: 1;
  }
  .brand__slogan {
    margin-top: 8px;
    font-family: "Montserrat", sans-serif;
    font-weight: 600;
    font-size: 14px;
    letter-spacing: 4px;
    color: var(--ink);
  }
  .person {
    position: absolute;
    right: 290px;
    top: 156px;
    text-align: right;
  }
  .person__name { font-weight: 700; font-size: 20px; color: var(--green-dark); }
  .person__title { font-size: 13px; color: var(--green-light); margin-top: 1px; }
  .person__address { font-size: 13px; margin-top: 10px; line-height: 1.3; }
  .divider {
    position: absolute;
    left: 255px; top: 150px;
    width: 1px; height: 80px;
    background: var(--rule);
  }
  .contacts {
    position: absolute;
    left: 268px; top: 148px;
    list-style: none;
    font-size: 13px;
    line-height: 20px;
  }
  .contacts li { display: flex; align-items: center; gap: 6px; }
  .contacts svg { width: 10px; height: 10px; fill: var(--ink-soft); }
  .swoosh { position: absolute; left: 0; bottom: 0; width: 530px; height: 110px; }

  /* Back */
  .mark {
    position: absolute;
    left: 50%; top: 48px;
    transform: translateX(-50%);
    width: 150px; height: 150px;
    border-radius: 50%;
    background: var(--green-light);
  }
  .back__name {
    position: absolute;
    left: 0; right: 0; top: 212px;
    text-align: center;
    font-family: "Montserrat", sans-serif;
    font-weight: 600;
    font-size: 20px;
    letter-spacing: 4px;
    color: var(--green-dark);
  }
  .back__web {
    position: absolute;
    left: 0; right: 0; bottom: 30px;
    text-align: center;
    font-family: "Montserrat", sans-serif;
    font-weight: 500;
    font-size: 15px;
    letter-spacing: 6px;
    color: var(--ink);
  }
</style>
</head>
<body>

<section class="card card--front">
  <div class="brand">
    <div class="brand__name">UPTICK INC</div>
    <div class="brand__slogan">MAKING TECHNOLOGY EASY</div>
  </div>

  <div class="person">
    <div class="person__name">Your Name</div>
    <div class="person__title">Title</div>
    <div class="person__address">00, Complex name<br>City, State 0042</div>
  </div>

  <div class="divider"></div>

  <ul class="contacts">
    <li><svg viewBox="0 0 10 10"><path d="M2 0h2l1 3-1.5 1a6 6 0 0 0 2.5 2.5L7 5l3 1v2a2 2 0 0 1-2 2A8 8 0 0 1 0 2a2 2 0 0 1 2-2z"/></svg>0123 456789</li>
    <li><svg viewBox="0 0 10 10"><path d="M2 1h6l2 4v4H0V5z"/></svg>0123 456789</li>
    <li><svg viewBox="0 0 10 10"><path d="M0 2h10v6H0z M0 2l5 3 5-3" stroke="#fff" stroke-width="0.8"/></svg>hello@uptick.com</li>
    <li><svg viewBox="0 0 10 10"><circle cx="5" cy="5" r="5"/></svg>www.uptick.com</li>
  </ul>

  <svg class="swoosh" viewBox="0 0 530 110" preserveAspectRatio="none" aria-hidden="true">
    <path d="M0 70 C 180 80, 380 60, 530 0 L530 110 L0 110 Z" fill="var(--green-dark)"/>
    <path d="M0 62 C 200 72, 390 50, 530 -2 C 390 44, 200 64, 0 66 Z" fill="var(--green-light)"/>
    <path d="M0 68 C 200 78, 390 56, 530 2 C 390 52, 200 72, 0 72 Z" fill="#ffffff"/>
  </svg>
</section>

<section class="card card--back">
  <div class="mark"></div>
  <div class="back__name">UPTICK INC</div>
  <div class="back__web">www.uptick.com</div>
</section>

</body>
</html>
```